1876 Basins & Spouts Business Card

I'm wanting to get a business card designed. Our business is 1876 Basins & Spouts
Details for the card:

1876 Basins & Spouts
Name: Harold Vesk
Email: harold@1876basinsandspouts.com.au
Website: www.1876basinsandspouts.com.au
Mobile: 0438 260 947
Phone: 02 7481 3926

Font of Basins & Spouts is called Snell Roundhand. Not sue what font logo text is.

I'm thinking two sided but it doesn't have to be.

```html
<!DOCTYPE html>
<html lang="en">
<head>
<meta charset="utf-8">
<title>1876 Basins &amp; Spouts Business Card</title>
<link rel="stylesheet" href="https://fonts.googleapis.com/css2?family=Open+Sans:wght@400&family=Pinyon+Script&display=swap">
<style>
  :root {
    --backdrop: #8c8c8c;
    --card-light: #efefef;
    --card-dark: #2d2a2a;
    --ornament-dark: #373434;
    --ink: #141414;
    --ink-soft: #333333;
    --rule: #9a9a9a;
    --paper-text: #ffffff;
    --tagline-dark: #d0d0d0;
  }
  html, body {
    margin: 0;
    width: 1200px;
    height: 1200px;
    overflow: hidden;
    background: var(--backdrop);
  }
  .canvas { position: relative; width: 1200px; height: 1200px; }
  .card {
    position: absolute;
    top: 310px;
    width: 364px;
    height: 594px;
    box-sizing: border-box;
    font-family: "Open Sans", sans-serif;
    text-align: center;
  }
  .card--front { left: 234px; background: var(--card-light); color: var(--ink); }
  .card--back { left: 628px; width: 368px; background: var(--card-dark); color: var(--paper-text); overflow: hidden; }

  .brand-name {
    position: absolute;
    left: 0; right: 0;
    font-family: "Open Sans", sans-serif;
    font-weight: 400;
    line-height: 32px;
    margin: 0;
  }
  .card--front .brand-name { top: 197px; font-size: 24px; color: var(--ink); }
  .tagline { position: absolute; left: 0; right: 0; margin: 0; font-size: 12px; line-height: 16px; }
  .card--front .tagline { top: 243px; color: var(--ink-soft); }

  .person-name {
    position: absolute;
    top: 345px; left: 0; right: 0;
    margin: 0;
    font-family: "Pinyon Script", cursive;
    font-size: 36px;
    font-weight: 400;
    color: var(--ink);
  }
  .contact-icons { position: absolute; top: 416px; left: 72px; }
  .contact-list {
    position: absolute;
    top: 450px; left: 0; right: 0;
    margin: 0; padding: 0;
    list-style: none;
    font-size: 16px;
    line-height: 21.5px;
    color: var(--ink);
  }

  .back-ornament { position: absolute; top: 0; left: 30px; width: 338px; height: 560px; }
  .card--back .brand-name { top: 479px; font-size: 26px; color: var(--paper-text); }
  .card--back .tagline { top: 527px; font-size: 12.5px; color: var(--tagline-dark); }
</style>
</head>
<body>
<div class="canvas">

  <section class="card card--front">
    <h1 class="brand-name">1876 Basins &amp; Spouts</h1>
    <p class="tagline">Pairing classic elegance with faithful everyday use</p>

    <h2 class="person-name">Harold Vesk</h2>

    <svg class="contact-icons" width="220" height="26" viewBox="0 0 220 26" aria-hidden="true">
      <line x1="0" y1="13" x2="54" y2="13" stroke="var(--rule)" stroke-width="1"/>
      <line x1="166" y1="13" x2="220" y2="13" stroke="var(--rule)" stroke-width="1"/>
      <g fill="var(--ink)">
        <rect x="56" y="2" width="22" height="22" rx="5"/>
        <rect x="84" y="2" width="22" height="22" rx="5"/>
        <rect x="112" y="2" width="22" height="22" rx="5"/>
        <rect x="140" y="2" width="22" height="22" rx="5"/>
      </g>
      <g fill="none" stroke="#ffffff" stroke-width="1.4">
        <path d="M61 11 q6 -5 12 0 M63 12 h8 l1 6 h-10 z"/>
        <rect x="90.5" y="6.5" width="9" height="13" rx="1.5"/>
        <rect x="116.5" y="8.5" width="13" height="9"/>
        <path d="M116.5 8.5 l6.5 5 l6.5 -5"/>
        <circle cx="151" cy="13" r="6"/>
      </g>
      <path d="M148 10 q3 1 2 4 q3 0 4 3 q-3 1 -6 -1 z" fill="#ffffff"/>
    </svg>

    <ul class="contact-list">
      <li>0438 260 947</li>
      <li>02 7481 3926</li>
      <li>harold@1876basinsandspouts.com.au</li>
      <li>www.1876basinsandspouts.com.au</li>
    </ul>
  </section>

  <section class="card card--back">
    <svg class="back-ornament" viewBox="0 0 338 560" role="img" aria-label="Faint ornate scrollwork decoration">
      <defs>
        <radialGradient id="ornamentGlow" cx="0.5" cy="0.45" r="0.6">
          <stop offset="0" stop-color="var(--ornament-dark)"/>
          <stop offset="1" stop-color="var(--card-dark)"/>
        </radialGradient>
      </defs>
      <rect width="338" height="560" fill="url(#ornamentGlow)"/>
    </svg>
    <h1 class="brand-name">1876 Basins &amp; Spouts</h1>
    <p class="tagline">Pairing classic elegance with faithful everyday use</p>
  </section>

</div>
</body>
</html>
```